BRAMBLEFORD CONSTRUCTIONS B-Card

I currently have a b-card design but will be removing the image (tree) from the logo and have text only.
I want the card to be classy and strong within the building and construction industry.
I will be using Spot UV on the cards as per the attached examples. I will also send through some sketched ideas that I have in mind.
The color blue is similar to the image (No. 6) attached images

Target Market(s)

middle to maturre aged.
Home Owners / Renovators and Builders

Industry/Entity Type

Construction

Contact Information for Business Card

BRAMBLEFORD CONSTRUCTIONS
Name: Gareth Pennick
Title: Project Manager
Mobile: 0427 351 804
Office: (08) 9316 5172
Address: 47C Corvell Street, Malaga WA 6090
Email: info@bramblefordhomes.com.au
PO Box: 3817 Malaga WA 6944

Colors
0592cd
33a6d7
85cae6
1b1b1b

Requirements
Must have
• 1. It must have spot UV on the front of card, maybe back of card too
• 2. I really like the blue on image 6. (or at least a really cool electric blue against the charcoal grey background)
• 3. The font must be slimline and modern. Easy to read
• 4. There must be no black used on the card... Only greys and dark charcoal greys
• 5. Use only the text from the logo "Brambleford Constructions" Not the image of the tree. I am wanting the b-cards to be more masculine.
Nice to have
• 1. I like the design concept on image 6. but happy to see what else you can do with the Spot UV
• 2. Unless you have a really cool idea of the image of the tree (from previous logo) Spot UV somewhere in the design concept thats original and different then I am keen to see what you come up with
• 3. Try changing the color of the logo eg. full white or Blue and white
• 4. Another option is to have the Brambleford Logo on the front of card with the spot UV in the background of text which we specialise in eg, Roofing, Ceiling, Insulation, Gutter Guards, Electrical, Insurance etc and we can add or reduce items as required. Similar to image 12.
Should not have
• Do not include the image of the tree from previous logo. unless you have a really cool idea of Spot UV somewhere in the design concept thats original and different.

```html
<!DOCTYPE html>
<html lang="en">
<head>
<meta charset="utf-8">
<title>Brambleford Constructions – Business Card</title>
<link rel="stylesheet" href="https://fonts.googleapis.com/css2?family=Open+Sans:wght@400;600;700&display=swap">
<style>
  :root {
    --bg: #3a3533;
    --card-blue: #2f6cb0;
    --brand-blue: #1f5fae;
    --foil: #d9dde2;
    --service-text: #e8eef6;
    --ink-grey: #4a4a4a;
    --paper: #ffffff;
  }
  * { margin: 0; padding: 0; box-sizing: border-box; }
  html, body {
    width: 1200px; height: 769px; overflow: hidden;
    background: var(--bg);
    font-family: "Open Sans", Arial, sans-serif;
  }
  .stage {
    position: relative; width: 1200px; height: 769px;
    display: flex; align-items: center; justify-content: center; gap: 44px;
  }
  .card {
    position: relative; width: 520px; height: 297px;
    box-shadow: 0 10px 28px rgba(0,0,0,.35);
  }
  /* front */
  .card--front { background: var(--card-blue); }
  .brand { position: absolute; font-weight: 700; line-height: 1; }
  .brand__name { display: block; font-size: 44px; letter-spacing: -1px; }
  .brand__sub  { display: block; font-size: 15px; letter-spacing: 13px; margin-top: 4px; }
  .card--front .brand { left: 96px; top: 92px; color: var(--foil); }
  .services {
    position: absolute; left: 0; right: 0; top: 192px;
    text-align: center; color: var(--service-text);
    font-size: 14px; line-height: 1.45;
  }
  /* back */
  .card--back { background: var(--paper); }
  .card--back .brand { right: 34px; top: 36px; color: var(--brand-blue); text-align: left; }
  .rule { position: absolute; left: 34px; right: 34px; height: 1.5px; background: var(--brand-blue); }
  .rule--top { top: 128px; }
  .rule--bottom { top: 266px; }
  .person {
    position: absolute; right: 34px; top: 136px;
    font-size: 13px; color: var(--ink-grey);
  }
  .person__name { color: var(--brand-blue); font-weight: 700; font-size: 17px; }
  .contacts {
    position: absolute; left: 34px; top: 142px; list-style: none;
    font-size: 12.5px; color: var(--ink-grey); line-height: 1.55;
  }
  .contacts li { display: flex; align-items: center; gap: 7px; }
  .contacts svg { width: 12px; height: 12px; fill: var(--brand-blue); flex: none; }
  .address {
    position: absolute; right: 34px; top: 196px; text-align: right;
    font-style: normal; font-size: 13.5px; color: var(--ink-grey); line-height: 1.4;
  }
</style>
</head>
<body>
<main class="stage">
  <section class="card card--front" aria-label="Card front">
    <div class="brand">
      <span class="brand__name">BRAMBLEFORD</span>
      <span class="brand__sub">CONSTRUCTIONS</span>
    </div>
    <p class="services">Roofing | Ceiling | Insulation | Gutter Guards<br>Electrical | Insurance etc</p>
  </section>

  <section class="card card--back" aria-label="Card back">
    <div class="brand">
      <span class="brand__name">BRAMBLEFORD</span>
      <span class="brand__sub">CONSTRUCTIONS</span>
    </div>
    <div class="rule rule--top"></div>
    <p class="person"><span class="person__name">Gareth Pennick</span> - Project Manager</p>
    <ul class="contacts">
      <li><svg viewBox="0 0 24 24" aria-hidden="true"><path d="M6.6 10.8a15 15 0 0 0 6.6 6.6l2.2-2.2a1 1 0 0 1 1-.25 11.4 11.4 0 0 0 3.6.57 1 1 0 0 1 1 1V20a1 1 0 0 1-1 1A17 17 0 0 1 3 4a1 1 0 0 1 1-1h3.5a1 1 0 0 1 1 1c0 1.25.2 2.45.57 3.6a1 1 0 0 1-.25 1z"/></svg>(08) 9316 5172</li>
      <li><svg viewBox="0 0 24 24" aria-hidden="true"><path d="M7 1h10a2 2 0 0 1 2 2v18a2 2 0 0 1-2 2H7a2 2 0 0 1-2-2V3a2 2 0 0 1 2-2zm0 3v14h10V4zm5 15.5a1 1 0 1 0 0 2 1 1 0 0 0 0-2z"/></svg>0427 351 804</li>
      <li><svg viewBox="0 0 24 24" aria-hidden="true"><path d="M2 5h20v14H2zm2 2v.5l8 5 8-5V7zm0 2.8V17h16V9.8l-8 5z"/></svg>info@bramblefordhomes.com.au</li>
    </ul>
    <address class="address">47C Corvell Street<br>Tarrowby WR 6071<br>PO Box 3817 Tarrowby WR 6983</address>
    <div class="rule rule--bottom"></div>
  </section>
</main>
</body>
</html>
```